Flat bootstrap design for existing site

I'm looking for a modern flat design based around an existing logo. This has to be a custom design (no external templates), and implemented into a bootstrap framework.

The logo is attached as 2 versions - choose whichever you want, that flows better with whatever design you choose.

Added screenshots of the existing site (currently using the default bootstrap layouts). Please make your designs around those pages in the screenshots (i.e. the homepage only has the postal code input and the header). The active page has 3 screenshots, because I wanted to illustrate the other states that would be visible (in the table rows).

This is a moving/junk removal website, just for some context.

Here's some example websites (flat designs) that I like, just to give you an idea of what I'm after.

https://www.plimvora.com/
https://dacklow.com/
https://trevanu.com/
https://quobrintal.com/en/

Coding

Coded - Design and coding required

Number of Pages Required

5+ page

Colors

Designer to choose colors to be used in the design.

Requirements
Must have
• It must be a modern/simple flat design, that is built around the existing logo (attached).
• It has to be implemented using bootstrap.

```html
<!DOCTYPE html>
<html lang="en">
<head>
<meta charset="utf-8">
<title>Sign In — Bravlo</title>
<link rel="stylesheet" href="https://fonts.googleapis.com/css2?family=Lato:wght@400;700;900&family=Open+Sans:wght@400&display=swap">
<style>
  :root {
    --sky: #6fd0f2;
    --sky-light: #7fd7f5;
    --sky-deep: #5ec8ee;
    --action: #48c8f5;
    --white: #ffffff;
    --ink: #262626;
    --label: #6b6b6b;
    --muted: #9a9a9a;
    --rule: #cfcfcf;
    --footer-rule: #9a9a9a;
    --footer-text: #666666;
  }
  * { box-sizing: border-box; margin: 0; padding: 0; }
  html, body {
    width: 1200px;
    height: 702px;
    overflow: hidden;
    background: var(--white);
    font-family: "Lato", Arial, sans-serif;
  }
  .page { position: relative; width: 1200px; height: 702px; }

  .site-header {
    position: absolute; left: 0; top: 0;
    width: 1200px; height: 105px;
  }
  .header-backdrop {
    position: absolute; inset: 0;
    background: linear-gradient(120deg, var(--sky-light) 0%, var(--sky) 45%, var(--sky-deep) 100%);
  }
  .brand {
    position: absolute; left: 99px; top: 30px;
    display: flex; align-items: center; gap: 10px;
    color: var(--white);
    font-weight: 900; font-size: 38px; letter-spacing: 1px;
    text-decoration: none; line-height: 44px;
  }
  .brand-dot {
    width: 14px; height: 14px; border-radius: 50%;
    background: var(--white);
  }
  .main-nav {
    position: absolute; right: 96px; top: 38px;
    display: flex; gap: 38px;
  }
  .main-nav a {
    color: var(--white); text-decoration: none;
    font-size: 15.5px; font-weight: 400;
    padding-bottom: 3px;
  }
  .main-nav a.is-current { border-bottom: 1px solid var(--white); }

  .page-title {
    position: absolute; left: 0; top: 162px; width: 1200px;
    text-align: center;
    font-size: 41px; font-weight: 900; color: var(--ink);
    line-height: 1;
  }

  .signin-card {
    position: absolute; left: 376px; top: 235px;
    width: 448px; height: 253px;
    background: var(--white);
    box-shadow: 0 1px 5px rgba(0,0,0,0.22);
  }
  .field {
    position: absolute; left: 53px; width: 343px;
    border: 0; border-bottom: 1px solid var(--rule);
    background: transparent;
    font-family: "Lato", Arial, sans-serif;
    font-size: 13.5px; color: var(--ink);
    height: 24px; padding: 0; outline: none;
  }
  .field::placeholder { color: var(--label); }
  .field-email { top: 52px; }
  .field-password { top: 107px; }
  .forgot-link {
    position: absolute; right: 52px; top: 151px;
    font-size: 13px; color: var(--muted); text-decoration: none;
  }
  .signin-button {
    position: absolute; left: 0; bottom: 0;
    width: 448px; height: 54px;
    border: 0; background: var(--action); color: var(--white);
    font-family: "Lato", Arial, sans-serif;
    font-size: 21px; font-weight: 400; letter-spacing: 0.5px;
  }

  .site-footer {
    position: absolute; left: 99px; top: 640px;
    width: 1002px; border-top: 1px solid var(--footer-rule);
  }
  .copyright {
    margin-top: 25px; text-align: center;
    font-family: "Open Sans", Arial, sans-serif;
    font-size: 12px; color: var(--footer-text);
  }
</style>
</head>
<body>
<div class="page">
  <header class="site-header">
    <div class="header-backdrop" role="img" aria-label="Light blue low-poly geometric header background"></div>
    <a class="brand" href="#"><span class="brand-dot"></span>BRAVLO</a>
    <nav class="main-nav">
      <a href="#">BOOK</a>
      <a href="#">HOW IT WOWS</a>
      <a href="#" class="is-current">BECOME A DRIVER</a>
      <a href="#">SIGN IN</a>
    </nav>
  </header>

  <h1 class="page-title">SIGN IN</h1>

  <form class="signin-card">
    <input class="field field-email" type="email" placeholder="Your Email Address">
    <input class="field field-password" type="password" placeholder="Password">
    <a class="forgot-link" href="#">Forgot your password?</a>
    <button class="signin-button" type="button">SIGN IN</button>
  </form>

  <footer class="site-footer">
    <p class="copyright">© Copyright 2017 Bravlo. All Rights Reserved</p>
  </footer>
</div>
</body>
</html>
```